Simple Logo Design for Semi-Clear Plastic Frosted Card stock

Create a business card on frosted plastic. compliment existing logo elements with a tree trunk, roots, or seed at the lower half and the full logo both on the front.

Contact information will go on a solid portion of the back of this design since this card stock is semi-transparent.

It is important to consider this plastic card stock medium in your design. I found helpful tips and guides listed at vellaprint-sample.net: be careful to understand ink printed on plastic cards cannot have too much of a consistent print area or risks peeling and fine lines can easily scratch off.
Updates

2" x 3.5" 20PT Clear Plastic Business cards with Round corners Please get info or templates here: https://www.vellaprint-sample.net/product-detail/2-x-35-20pt-clear-plastic-business-cards-with-round-corners

Target Market(s)

Not for profit- religion

Industry/Entity Type

Business

Must include complementary elements to the existing logo

Font styles to use
Decorative

Colors
000000

Requirements
Must have
• Elements of community, nature and oneness. Such as: seed, roots, tree trunk, etc.
• Three lines of space on the back for Name, Title, Phone Number.
Nice to have
• I like a light use of decorative elements
Should not have
• No eyes, from faces or animals.

```html
<!DOCTYPE html>
<html lang="en">
<head>
<meta charset="utf-8">
<title>Gathered Roots – Business Card</title>
<link href="https://fonts.googleapis.com/css2?family=Open+Sans:wght@400;600&family=Questrial&display=swap" rel="stylesheet">
<style>
  :root {
    --teal: #226b69;
    --green: #4a9a3f;
    --frost: #f3ecec;
    --paper: #ffffff;
    --stage: #e7e4e2;
    --ink-soft: #3d4a48;
    --ghost: #ececec;
  }
  html, body {
    margin: 0;
    padding: 0;
    width: 1200px;
    height: 900px;
    overflow: hidden;
    background: var(--stage);
  }
  .canvas {
    position: relative;
    width: 1200px;
    height: 900px;
  }
  .card {
    position: absolute;
    border-radius: 6px;
    overflow: hidden;
    box-shadow: 0 6px 18px rgba(0,0,0,0.12);
  }
  .card--front {
    left: 78px;
    top: 35px;
    width: 587px;
    height: 363px;
    background: var(--frost);
  }
  .card--back {
    left: 388px;
    top: 505px;
    width: 567px;
    height: 352px;
    background: var(--paper);
  }
  .card__waves {
    position: absolute;
    inset: 0;
    width: 100%;
    height: 100%;
  }
  .holder {
    position: absolute;
    left: 40px;
    top: 34px;
    color: #fff;
    font-family: "Open Sans", sans-serif;
  }
  .holder__name {
    margin: 0;
    font-size: 22px;
    font-weight: 600;
    line-height: 1.2;
  }
  .holder__title {
    margin: 2px 0 0;
    font-size: 15px;
    font-weight: 400;
  }
  .contact {
    position: absolute;
    right: 36px;
    bottom: 30px;
    margin: 0;
    display: flex;
    align-items: center;
    gap: 8px;
    color: #fff;
    font-family: "Open Sans", sans-serif;
    font-size: 15px;
  }
  .contact__icon { width: 13px; height: 13px; }
  .brand {
    position: absolute;
    display: flex;
    align-items: center;
    gap: 20px;
  }
  .card--front .brand { left: 52px; top: 150px; }
  .brand__dot {
    width: 96px;
    height: 96px;
    border-radius: 50%;
    background: var(--green);
    flex: none;
  }
  .brand__text { font-family: "Questrial", sans-serif; }
  .brand__name {
    margin: 0;
    color: var(--teal);
    font-size: 34px;
    font-weight: 400;
    letter-spacing: 0.5px;
    line-height: 1;
    white-space: nowrap;
  }
  .brand__tagline {
    margin: 4px 0 0;
    color: var(--ink-soft);
    font-size: 12px;
    letter-spacing: 0.6px;
    text-align: center;
    white-space: nowrap;
  }
  .back__mark {
    position: absolute;
    left: -40px;
    top: 10px;
    width: 380px;
    height: 380px;
    border-radius: 50%;
    background: var(--ghost);
  }
  .card--back .brand {
    right: 40px;
    bottom: 50px;
  }
  .card--back .brand__name { font-size: 38px; }
  .card--back .brand__tagline { font-size: 14px; }
</style>
</head>
<body>
<main class="canvas">
  <section class="card card--front" aria-label="Card front">
    <svg class="card__waves" viewBox="0 0 587 363" preserveAspectRatio="none" aria-hidden="true">
      <path d="M0 0 H587 V40 C500 48 430 90 350 118 C290 138 230 140 170 136 C110 132 50 128 0 126 Z" fill="#4a9a3f"/>
      <path d="M0 0 H450 C400 25 350 80 300 105 C250 125 200 125 150 122 C90 118 40 112 0 108 Z" fill="#226b69"/>
      <path d="M0 363 H587 V252 C520 246 450 246 380 260 C260 285 140 330 0 340 Z" fill="#4a9a3f"/>
      <path d="M190 363 C270 330 340 290 420 268 C480 252 540 252 587 260 V363 Z" fill="#226b69"/>
    </svg>
    <div class="holder">
      <p class="holder__name">Daniel Reyes</p>
      <p class="holder__title">Managing Director</p>
    </div>
    <div class="brand">
      <span class="brand__dot"></span>
      <div class="brand__text">
        <p class="brand__name">GATHERED ROOTS</p>
        <p class="brand__tagline">GROWTH, FELLOWSHIP &amp; STILLNESS</p>
      </div>
    </div>
    <p class="contact">
      (055)-318-2046
      <svg class="contact__icon" viewBox="0 0 24 24" aria-hidden="true"><path fill="#fff" d="M6.6 10.8a15.1 15.1 0 0 0 6.6 6.6l2.2-2.2c.3-.3.7-.4 1-.2 1.1.4 2.3.6 3.6.6.6 0 1 .4 1 1V20c0 .6-.4 1-1 1A17 17 0 0 1 3 4c0-.6.4-1 1-1h3.5c.6 0 1 .4 1 1 0 1.3.2 2.5.6 3.6.1.3 0 .7-.2 1z"/></svg>
    </p>
  </section>

  <section class="card card--back" aria-label="Card back">
    <span class="back__mark"></span>
    <div class="brand">
      <div class="brand__text">
        <p class="brand__name">GATHERED ROOTS</p>
        <p class="brand__tagline">GROWTH, FELLOWSHIP &amp; STILLNESS</p>
      </div>
    </div>
  </section>
</main>
</body>
</html>
```